Wedding Ceremony Equipment Hire Business Card

I need a business card design for a new business I created called Vowline Rentals. We hire out Wedding Ceremony equipment and decorations mainly for beach and garden wedding ceremonies that include delivery, set up and dismantle. We do offer DIY Chair Hire as well.
I'd like to have a similar design and colours to our website:
www.vowlinerentals.com.au
If possible would like the front to incorporate our information and logo and the back to have two faded example pictures of our wedding ceremonies.
I have attached two photos and our logo. Please let me know if you need a better pic of our logo though.

Target Market(s)

Newly engaged couples, aged 25 and upwards

Industry/Entity Type

Wedding

Contact Information for Business Card

Vowline Rentals
Mira Holt
0412 908 146
hello@vowlinerentals.com.au
www.vowlinesocial.com/VowlineRentals

```html
<!DOCTYPE html>
<html lang="en">
<head>
<meta charset="utf-8">
<title>Vowline Rentals – Business Card</title>
<link rel="stylesheet" href="https://fonts.googleapis.com/css2?family=Cormorant+Garamond:ital,wght@1,500;1,600&display=swap">
<style>
  :root {
    --page: #ffffff;
    --mint: #5ff27a;
    --mint-soft: #7df592;
    --charcoal: #1e2426;
    --ink: #1b1f20;
    --paper-text: #ffffff;
    --accent: #5ff27a;
  }
  * { margin: 0; padding: 0; box-sizing: border-box; }
  html, body {
    width: 1200px; height: 741px; overflow: hidden;
    background: var(--page);
    font-family: "Cormorant Garamond", Georgia, serif;
    font-style: italic;
  }
  .card {
    position: absolute; left: 144px; top: 85px;
    width: 945px; height: 578px;
    overflow: hidden;
  }
  .card__top {
    position: absolute; left: 0; top: 0;
    width: 100%; height: 352px;
    background: var(--mint);
  }
  .card__ornament {
    position: absolute; left: 60px; top: 0;
    width: 420px; height: 352px;
    background: radial-gradient(ellipse at 45% 45%, var(--mint-soft) 0%, rgba(125,245,146,0.5) 45%, rgba(95,242,122,0) 72%);
  }
  .brand-name {
    position: absolute; left: 56px; top: 62px;
    font-size: 64px; font-weight: 600; line-height: 1;
    color: var(--ink);
  }
  .tagline {
    position: absolute; left: 63px; top: 195px;
    font-size: 24px; font-weight: 600; line-height: 31px;
    color: var(--ink);
  }
  .card__bottom {
    position: absolute; left: 0; top: 352px;
    width: 100%; height: 226px;
    background: var(--charcoal);
    color: var(--paper-text);
  }
  .contact {
    position: absolute; left: 271px; top: 16px;
    width: 404px; text-align: center;
  }
  .contact__name {
    font-size: 29px; font-weight: 600; line-height: 1.2;
    padding-bottom: 8px;
    border-bottom: 3px solid var(--accent);
  }
  .contact__details {
    margin-top: 8px;
    font-size: 23px; font-weight: 600; line-height: 29px;
  }
  .links {
    position: absolute; left: 17px; top: 166px;
    font-size: 23px; font-weight: 600; line-height: 26px;
  }
  .links a { color: var(--accent); text-decoration: none; }
</style>
</head>
<body>
  <div class="card">
    <section class="card__top">
      <div class="card__ornament" role="img" aria-label="Faint pale swirl ornament behind the brand name"></div>
      <div class="brand-name">Vowline Rentals</div>
      <p class="tagline">We pride ourselves on our friendly but professional services<br>in ensuring your special day is just as you imagined it to be.</p>
    </section>
    <section class="card__bottom">
      <div class="contact">
        <div class="contact__name">Mira Holt</div>
        <div class="contact__details">
          Phone: 0412 908 146<br>
          Email: hello@vowlinerentals.com.au
        </div>
      </div>
      <div class="links">
        Visit our Website: <a href="#">www.vowlinerentals.com.au</a><br>
        Our Social Page: <a href="#">www.vowlinesocial.com/VowlineRentals</a>
      </div>
    </section>
  </div>
</body>
</html>
```